Flyer for the Lumen 2025 Conference

I am looking to produce a flyer for our upcoming conference, Lumen 2025. This is an annual conference that we plan to publicize on social media. The ideal designer will create a flyer that is eye-catching and effectively communicates the key information. Please see attached our logo, speaker photo, and flyer content.

Target Market(s)

All demographics

Industry/Entity Type

Christian

Font styles to use
Sans Serif

Requirements
Should not have
• Cross, church

```html
<!DOCTYPE html>
<html lang="en">
<head>
<meta charset="utf-8">
<title>Lumen 2025 Conference Flyer</title>
<link href="https://fonts.googleapis.com/css2?family=Bebas+Neue&family=Lexend:wght@500;600;700&family=Oswald:wght@500;600&display=swap" rel="stylesheet">
<style>
  :root {
    --orange: #f7931e;
    --navy: #053a60;
    --navy-deep: #0b2f5a;
    --blue-top: #16487a;
    --blue-bottom: #2a4a8c;
    --white: #ffffff;
    --time-bar: #1a5aa0;
  }
  * { margin: 0; padding: 0; box-sizing: border-box; }
  html, body { width: 890px; height: 1200px; overflow: hidden; }
  body { font-family: "Lexend", sans-serif; color: var(--white); }
  .flyer {
    position: relative; width: 890px; height: 1200px; overflow: hidden;
    background: linear-gradient(180deg, var(--blue-top) 0%, #1f5089 45%, var(--blue-bottom) 100%);
  }
  .brand {
    position: absolute; left: 0; top: 0; width: 272px; height: 130px;
    background: var(--white); border-radius: 0 0 95px 0;
    display: flex; align-items: center; gap: 10px; padding-left: 30px;
  }
  .brand-dot { width: 18px; height: 18px; border-radius: 50%; background: var(--orange); }
  .brand-name { font-family: "Lexend", sans-serif; font-weight: 600; font-size: 40px; color: var(--navy); letter-spacing: 1px; }
  .edition { position: absolute; right: 45px; top: 22px; text-align: right; font-weight: 700; line-height: 0.95; }
  .edition-name { color: var(--orange); font-size: 46px; }
  .edition-year { color: var(--white); font-size: 64px; }
  .kicker {
    position: absolute; left: 0; right: 0; top: 160px; display: flex; align-items: center; justify-content: center; gap: 14px;
    font-family: "Bebas Neue", sans-serif; font-size: 66px; line-height: 1;
    color: #fbd9a5;
  }
  .kicker-text { background: linear-gradient(180deg, #fff 0%, #fde4bd 50%, var(--orange) 100%); -webkit-background-clip: text; background-clip: text; color: transparent; }
  .kicker-line { width: 70px; height: 3px; background: linear-gradient(90deg, transparent, var(--orange)); }
  .kicker-line.right { background: linear-gradient(90deg, var(--orange), transparent); }
  .title-band {
    position: absolute; left: 0; top: 228px; width: 890px; height: 101px; background: var(--navy);
    display: flex; align-items: center; justify-content: center;
    font-family: "Bebas Neue", sans-serif; font-size: 104px; line-height: 1; padding-top: 8px; white-space: nowrap;
  }
  .title-band .accent { color: var(--orange); }
  .halo { position: absolute; left: 0; top: 329px; }
  .speaker-photo {
    position: absolute; left: 240px; top: 390px; width: 400px; height: 560px;
    border-radius: 200px 200px 30px 30px;
    background: linear-gradient(180deg, #8a6b55 0%, #3a6fc4 40%, #1f5fb8 75%, rgba(31,80,137,0) 100%);
  }
  .speaker { position: absolute; left: 0; right: 0; top: 706px; text-align: center; font-weight: 700; line-height: 1.05; }
  .speaker-label { color: var(--orange); font-size: 28px; }
  .speaker-name { font-size: 44px; margin-top: 10px; }
  .schedule { position: absolute; left: 36px; top: 880px; display: flex; gap: 40px; }
  .day { width: 163px; }
  .day-name { color: var(--orange); font-size: 20px; font-weight: 500; }
  .day-month { font-size: 24px; font-weight: 600; margin-top: 2px; }
  .day-number { color: var(--orange); font-size: 118px; font-weight: 700; line-height: 0.9; letter-spacing: -3px; margin-top: 4px; }
  .day-time {
    margin-top: 8px; height: 30px; background: var(--time-bar); border-top: 2px solid var(--orange);
    display: flex; align-items: center; justify-content: center; font-size: 14px; font-weight: 500;
  }
  .app-promo {
    position: absolute; left: 670px; top: 812px; width: 220px; height: 280px;
    border-radius: 40px 0 0 0;
    background: linear-gradient(160deg, #e9c2a6 0%, #d9a98a 60%, #c99478 100%);
  }
  .app-screen {
    position: absolute; left: 690px; top: 820px; width: 148px; height: 270px;
    background: var(--white); border: 6px solid #1c1c1c; border-radius: 22px 22px 0 0;
    text-align: center; padding: 26px 8px 0;
    font-family: "Oswald", sans-serif; font-weight: 500; color: var(--navy); font-size: 14px; line-height: 1.2;
  }
  .app-screen-brand { display: flex; align-items: center; justify-content: center; gap: 5px; font-family: "Lexend", sans-serif; font-weight: 600; font-size: 18px; margin-bottom: 12px; }
  .app-screen-brand span { width: 8px; height: 8px; border-radius: 50%; background: var(--orange); }
  .app-screen .accent { color: var(--orange); }
  .store-badge { width: 96px; height: 26px; margin: 8px auto 0; background: #111; border-radius: 4px; }
  .venue {
    position: absolute; left: 25px; top: 1080px; width: 838px; height: 49px;
    background: var(--white); border-radius: 24px; border-bottom: 4px solid var(--orange);
    display: flex; align-items: center; justify-content: center; gap: 18px;
    font-family: "Oswald", sans-serif; font-weight: 500; font-size: 20px; color: var(--navy);
  }
  .contact-bar {
    position: absolute; left: 0; top: 1135px; width: 890px; height: 65px; background: var(--navy-deep);
    display: flex; align-items: center;
  }
  .contact-item { display: flex; align-items: center; justify-content: center; gap: 12px; height: 100%; }
  .contact-item.phone { width: 332px; font-family: "Lexend", sans-serif; font-size: 24px; font-weight: 500; }
  .contact-item.email { width: 297px; font-family: "Oswald", sans-serif; font-size: 22px; font-weight: 500; }
  .contact-item.web { width: 261px; font-family: "Oswald", sans-serif; font-size: 22px; font-weight: 500; }
  .divider { width: 2px; height: 48px; background: var(--orange); }
</style>
</head>
<body>
<div class="flyer">
  <div class="brand"><span class="brand-dot"></span><span class="brand-name">VERANE</span></div>

  <div class="edition">
    <div class="edition-name">LUMEN</div>
    <div class="edition-year">2025</div>
  </div>

  <div class="kicker">
    <span class="kicker-line"></span>
    <span class="kicker-text">A Prophetic Conference</span>
    <span class="kicker-line right"></span>
  </div>

  <div class="title-band">THE VOICE OF&nbsp;<span class="accent">THE LORD</span></div>

  <svg class="halo" width="890" height="760" viewBox="0 0 890 760" aria-hidden="true">
    <circle cx="439" cy="360" r="400" fill="#2c5a92" opacity="0.35"/>
    <circle cx="439" cy="360" r="360" fill="#3c6398" opacity="0.45"/>
    <circle cx="439" cy="360" r="320" fill="#4e6c9e" opacity="0.55"/>
    <circle cx="439" cy="360" r="260" fill="#eef1f6"/>
    <rect x="0" y="520" width="890" height="240" fill="url(#fade)"/>
    <defs>
      <linearGradient id="fade" x1="0" y1="0" x2="0" y2="1">
        <stop offset="0" stop-color="#22508a" stop-opacity="0"/>
        <stop offset="0.5" stop-color="#23508a" stop-opacity="0.9"/>
        <stop offset="1" stop-color="#274c8b"/>
      </linearGradient>
    </defs>
  </svg>

  <div class="speaker-photo" role="img" aria-label="Portrait photo of the speaker in a blue suit"></div>

  <div class="speaker">
    <div class="speaker-label">SPEAKER</div>
    <div class="speaker-name">PROPHET<br>SAMUEL ADEYO</div>
  </div>

  <div class="schedule">
    <div class="day">
      <div class="day-name">Friday</div>
      <div class="day-month">DECEMBER</div>
      <div class="day-number">26</div>
      <div class="day-time">6:30 PM - 9:00 PM</div>
    </div>
    <div class="day">
      <div class="day-name">Saturday</div>
      <div class="day-month">DECEMBER</div>
      <div class="day-number">27</div>
      <div class="day-time">5:30 PM - 8:00 PM</div>
    </div>
    <div class="day">
      <div class="day-name">Sunday</div>
      <div class="day-month">DECEMBER</div>
      <div class="day-number">28</div>
      <div class="day-time">4:30 PM - 7:00 PM</div>
    </div>
  </div>

  <div class="app-promo" role="img" aria-label="Photo of hands holding a smartphone showing the app"></div>
  <div class="app-screen">
    <div class="app-screen-brand"><span></span>VERANE</div>
    Download the<br><span class="accent">VERANE App</span><br>to stay updated on<br>the event
    <div class="store-badge"></div>
    <div class="store-badge"></div>
  </div>

  <div class="venue">
    <svg width="22" height="28" viewBox="0 0 22 28" aria-hidden="true">
      <path d="M11 1C5.5 1 1 5.4 1 10.8 1 18 11 27 11 27s10-9 10-16.2C21 5.4 16.5 1 11 1z" fill="#f7931e"/>
      <circle cx="11" cy="10.5" r="4" fill="#fff"/>
    </svg>
    <span>The Harborview Performing Arts Center, 250 Linden Avenue, Fairhaven, Maine 04000</span>
  </div>

  <div class="contact-bar">
    <div class="contact-item phone">
      <svg width="22" height="22" viewBox="0 0 24 24" aria-hidden="true">
        <path d="M6.6 10.8a15.1 15.1 0 006.6 6.6l2.2-2.2c.3-.3.7-.4 1-.2 1.1.4 2.3.6 3.6.6.6 0 1 .4 1 1V20c0 .6-.4 1-1 1A17 17 0 013 4c0-.6.4-1 1-1h3.5c.6 0 1 .4 1 1 0 1.3.2 2.5.6 3.6.1.3 0 .7-.2 1z" fill="#f7931e"/>
      </svg>
      <span>207 555 0142</span>
    </div>
    <span class="divider"></span>
    <div class="contact-item email">
      <svg width="24" height="18" viewBox="0 0 24 18" aria-hidden="true">
        <rect x="1" y="1" width="22" height="16" rx="1" fill="none" stroke="#f7931e" stroke-width="2"/>
        <path d="M1 2l11 8 11-8" fill="none" stroke="#f7931e" stroke-width="2"/>
      </svg>
      <span>contact@verane.org</span>
    </div>
    <span class="divider"></span>
    <div class="contact-item web">
      <svg width="22" height="22" viewBox="0 0 24 24" aria-hidden="true">
        <g fill="none" stroke="#f7931e" stroke-width="1.8">
          <circle cx="12" cy="12" r="10"/>
          <ellipse cx="12" cy="12" rx="4.5" ry="10"/>
          <path d="M2 12h20M4 7h16M4 17h16"/>
        </g>
      </svg>
      <span>www.verane.org</span>
    </div>
  </div>
</div>
</body>
</html>
```